Heritage Hollow Business Cards

Require a business card design. <br/><br/>Needs to include logo (either round or long version) plus these details:<br/>Maya Torvell<br/>Heritage Hollow<br/>maya@kelvadtrading.com.au<br/>02 6481 7395<br/>PO Box Glenwarra NSW 2791<br/>www.heritagehollow.com.au<br/><br/>I need in an editable format so that I can create for multiple staff members. <br/><br/>

Target Market(s)

We are an online store selling renovation products to home owners are builders. Looking for a classic classy design.

Industry/Entity Type

Home And Garden

Contact Information for Business Card

Maya Torvell
Heritage Hollow
maya@kelvadtrading.com.au
02 6481 7395
PO Box Glenwarra NSW 2791
www.heritagehollow.com.au

Colors

Designer to choose colors to be used in the design.

Requirements
Must have
• Must include Logo.

```html
<!DOCTYPE html>
<html lang="en">
<head>
<meta charset="utf-8">
<title>Heritage Hollow Business Cards</title>
<link href="https://fonts.googleapis.com/css2?family=Josefin+Sans:wght@400&family=Open+Sans:wght@400;600&display=swap" rel="stylesheet">
<style>
  :root {
    --backdrop: #c0c0c0;
    --card: #ffffff;
    --sage: #52705f;
    --ink: #131317;
    --paper-text: #ffffff;
  }
  html, body {
    margin: 0;
    padding: 0;
    width: 933px;
    height: 1200px;
    overflow: hidden;
    background: var(--backdrop);
  }
  .sheet {
    position: relative;
    width: 933px;
    height: 1200px;
  }
  .card {
    position: absolute;
    left: 190px;
    width: 535px;
    height: 305px;
    display: block;
  }
  .card--front { top: 212px; }
  .card--back { top: 658px; }
  .card-face { fill: var(--card); }
  .sage-panel { fill: var(--sage); }
  .ink-band { fill: var(--ink); }
  .brand-ring { fill: none; stroke: var(--ink); stroke-width: 0.8; }
  .brand-name {
    font-family: "Open Sans", sans-serif;
    font-weight: 600;
    fill: var(--ink);
  }
  .web-address, .contact-line {
    font-family: "Open Sans", sans-serif;
    font-weight: 400;
    fill: var(--paper-text);
  }
  .web-address { font-size: 15px; }
  .contact-line { font-size: 11.5px; }
  .staff-name {
    font-family: "Josefin Sans", sans-serif;
    font-weight: 400;
    font-size: 28px;
    letter-spacing: 1px;
    fill: var(--paper-text);
  }
  .staff-role {
    font-family: "Open Sans", sans-serif;
    font-size: 12.5px;
    fill: var(--paper-text);
  }
  .icon { fill: var(--paper-text); }
  .icon-stroke { fill: none; stroke: var(--paper-text); stroke-width: 1.3; }
</style>
</head>
<body>
<main class="sheet">

  <svg class="card card--front" viewBox="0 0 535 305" aria-label="Card front">
    <rect class="card-face" width="535" height="305"/>
    <circle class="brand-ring" cx="284" cy="128" r="104"/>
    <text class="brand-name" x="284" y="132" font-size="31" text-anchor="middle">Heritage</text>
    <text class="brand-name" x="284" y="166" font-size="31" text-anchor="middle">Hollow</text>
    <rect class="ink-band" x="260" y="263" width="275" height="19"/>
    <polygon class="sage-panel" points="0,239 263,239 306,305 0,305"/>
    <text class="web-address" x="19" y="276">www.heritagehollow.com.au</text>
  </svg>

  <svg class="card card--back" viewBox="0 0 535 305" aria-label="Card back">
    <rect class="card-face" width="535" height="305"/>
    <circle class="brand-ring" cx="100" cy="104" r="13"/>
    <text class="brand-name" x="124" y="117" font-size="36">Heritage Hollow</text>

    <rect class="ink-band" x="200" y="149" width="335" height="19"/>
    <rect class="ink-band" x="200" y="188" width="335" height="21"/>
    <rect class="ink-band" x="200" y="228" width="335" height="21"/>
    <rect class="ink-band" x="200" y="267" width="335" height="20"/>

    <polygon class="sage-panel" points="0,131 213,131 306,305 0,305"/>

    <text class="staff-name" x="31" y="219">MAYA TORVELL</text>
    <text class="staff-role" x="31" y="234">Director</text>

    <g class="contact-row">
      <path class="icon" d="M308 151.5c1.2-.6 2.2-.6 2.8.4l1.6 2.6c.4.8.2 1.5-.6 2l-1.1.7c.6 1.8 2.2 3.7 4 4.6l.8-1c.6-.7 1.3-.8 2-.3l2.4 1.8c.8.6.8 1.5.1 2.5-1.2 1.5-3 1.8-4.8 1-3.8-1.8-6.7-5.2-8-9.2-.5-1.9-.1-4 .8-5.1z"/>
      <text class="contact-line" x="340" y="163">02 6481 7395</text>
    </g>
    <g class="contact-row">
      <rect class="icon-stroke" x="305" y="193.5" width="15" height="10"/>
      <path class="icon-stroke" d="M305 193.5l7.5 6 7.5-6M305 203.5l5.5-5M320 203.5l-5.5-5"/>
      <text class="contact-line" x="337" y="203">maya@kelvadtrading.com.au</text>
    </g>
    <g class="contact-row">
      <circle class="icon-stroke" cx="313" cy="238.5" r="6.5"/>
      <path class="icon" d="M309 235c2-1 3.5 0 4 1.5s-1 2-1 3.5-2 1.5-3-.5zM314.5 234c1.5 0 3 .8 3.5 2l-2 .8z"/>
      <text class="contact-line" x="337" y="242.5">www.heritagehollow.com.au</text>
    </g>
    <g class="contact-row">
      <path class="icon" d="M313 269c-3 0-5.3 2.3-5.3 5.2 0 3.6 5.3 9.3 5.3 9.3s5.3-5.7 5.3-9.3c0-2.9-2.3-5.2-5.3-5.2zm0 7.4a2.2 2.2 0 1 1 0-4.4 2.2 2.2 0 0 1 0 4.4z"/>
      <text class="contact-line" x="336" y="281.5">PO Box Glenwarra NSW 2791</text>
    </g>
  </svg>

</main>
</body>
</html>
```